Glimmer Step Blog

Need a blog design. I am the first GlimStep blogger-very exciting! My first project will be reporting on Twirling Under Lanterns which premieres this Monday-St. Patrick's Day. I am looking for an exciting format to represent my new venture. I will be focusing on ballroom dance fashion-I like creativity and look for something with a cool color scheme, artistic, could be modern or really open for someone to interpret this concept in a creative way. The blog name is GlimStep.

Fashion

```html
<!DOCTYPE html>
<html lang="en">
<head>
<meta charset="utf-8">
<title>GlimStep — Glimmer Step Blog</title>
<link href="https://fonts.googleapis.com/css2?family=Gelasio:wght@400;700&family=Open+Sans:ital,wght@0,400;0,600;1,400&display=swap" rel="stylesheet">
<style>
:root{
  --navy:#0b3550;
  --navy-deep:#082a40;
  --ink:#2b2b2b;
  --body:#6a6a6a;
  --muted:#8a8a8a;
  --rule:#d9d9d9;
  --accent:#e2483a;
  --panel:#f3f3f3;
  --panel-edge:#c9c9c9;
  --social-blue:#3b5a9a;
  --sky:#17a9e0;
  --sky-line:#5cc5ec;
  --white:#ffffff;
}
*{box-sizing:border-box;margin:0;padding:0}
html,body{width:1200px;height:2985px;overflow:hidden;background:var(--white)}
body{position:relative;font-family:"Open Sans",Arial,sans-serif;color:var(--body)}

/* header */
.site-header{position:absolute;left:0;top:0;width:1200px;height:110px;background:var(--navy)}
.brand{position:absolute;left:110px;top:18px;font-family:"Gelasio",Georgia,serif;font-weight:700;font-size:48px;color:var(--white);letter-spacing:.5px}
.social-tabs{position:absolute;right:128px;top:0;display:flex;gap:4px}
.social-tabs span{display:block;width:28px;height:42px;background:var(--white);clip-path:polygon(0 0,100% 0,100% 100%,50% 82%,0 100%)}

/* posts */
.post{position:absolute;left:110px;width:680px}
.post h2{font-family:"Gelasio",Georgia,serif;font-weight:400;font-size:32px;line-height:40px;letter-spacing:-.4px;color:var(--ink)}
.meta{display:flex;align-items:center;height:32px;border-top:1px dashed var(--rule);border-bottom:1px dashed var(--rule);font-size:12px;color:var(--muted);margin-top:16px}
.meta .comments{margin-left:26px;display:flex;align-items:center;gap:6px}
.share{margin-left:auto;display:flex;gap:6px;align-items:center}
.share b{font-weight:600;font-size:10px;height:16px;line-height:14px;padding:0 6px;border:1px solid #c6cbd6;background:#eef1f6;color:#3b4a6b;border-radius:2px}
.share i{font-style:normal;font-size:9px;height:16px;line-height:14px;padding:0 5px;border:1px solid var(--rule);color:var(--muted)}
.photo{display:block;margin-top:22px}
.post p{font-size:13px;line-height:20px;margin-top:20px;color:var(--body)}
.post p + p{margin-top:14px}
.more{display:inline-flex;align-items:center;gap:12px;margin-top:22px;font-size:13px;color:var(--accent)}
.divider{position:absolute;left:340px;width:220px;height:2px;background:#dadada}

/* sidebar */
.sidebar{position:absolute;left:830px;top:190px;width:278px;height:1322px;background:linear-gradient(to right,var(--white),var(--panel));border:2px solid var(--panel-edge);border-radius:3px}
.ad-box{position:absolute;left:16px;top:22px;width:244px;height:202px;background:var(--white);border:1px solid #dcdcdc;display:flex;align-items:center;justify-content:center;gap:8px}
.ad-box .dot{width:14px;height:14px;border-radius:50%;background:#2aa6dd}
.ad-box .name{font-size:30px;font-weight:600;color:#5a6470}
.tabs{position:absolute;left:16px;top:270px;width:244px;height:42px;display:flex}
.tabs span{flex:1;display:flex;align-items:center;justify-content:center;font-size:17px}
.tabs .on{background:var(--navy);color:var(--white)}
.tabs .off{background:#e2e4e6;color:#6b7680;border:1px solid #cfd3d6}
.news{position:absolute;left:16px;top:330px;width:244px}
.news li{list-style:none;display:flex;gap:10px;height:92px;border-bottom:1px solid #dcdcdc;padding-top:6px}
.news li + li{padding-top:10px}
.news li:last-child{border-bottom:0;height:80px}
.thumb{width:64px;height:46px;flex:none;background:linear-gradient(135deg,#2a1c18,#8a5a3a);border:2px solid var(--white);box-shadow:0 0 0 1px #ccc}
.news em{display:block;font-size:11px;color:var(--muted)}
.news strong{display:block;font-weight:400;font-size:12px;line-height:16px;color:#333}
.read-all{position:absolute;left:18px;top:608px;font-size:13px;color:var(--accent);display:flex;gap:10px;align-items:center}
.welcome{position:absolute;left:18px;top:676px;width:240px}
.welcome h3{font-family:"Gelasio",Georgia,serif;font-weight:400;font-size:25px;line-height:31px;color:var(--ink)}
.welcome p{font-size:11.5px;line-height:15px;color:#444;margin-top:18px}
.welcome p + p{margin-top:14px}
.fb-btn{position:absolute;left:8px;top:966px;width:260px;height:40px;background:var(--social-blue);color:var(--white);font-size:15px;display:flex;align-items:center;padding-left:26px;gap:10px;border-radius:2px}
.fb-btn .sq{width:14px;height:14px;background:var(--white);opacity:.9}
.fan{position:absolute;left:16px;top:1034px;width:244px}
.fan-head{display:flex;gap:10px;align-items:center;padding-bottom:12px;border-bottom:1px solid #e3e3e3}
.fan-head .mark{font-family:"Gelasio",Georgia,serif;font-weight:700;font-size:30px;color:var(--navy-deep)}
.fan-head b{display:block;font-size:12px;color:var(--social-blue)}
.fan-head i{display:inline-block;font-style:normal;font-size:9px;border:1px solid #c6cbd6;background:#eef1f6;padding:0 4px;color:#3b4a6b}
.fan small{display:block;font-size:9px;margin:8px 0;color:#555}
.faces{display:grid;grid-template-columns:repeat(4,1fr);gap:8px 12px}
.faces span{display:block;text-align:center;font-size:9px;color:#333}
.faces span::before{content:"";display:block;width:44px;height:44px;margin:0 auto 4px;background:linear-gradient(135deg,#5b3a2c,#b48a6a)}
.fan .plugin{margin-top:10px;padding-top:8px;border-top:1px solid #e3e3e3;font-size:9px;color:#555}

.chirper{position:absolute;left:832px;top:1534px;width:276px;height:410px;background:var(--sky);border:2px solid #0f95c8}
.chirper h4{font-weight:400;font-size:18px;color:var(--white);padding:26px 0 0 64px;position:relative}
.chirper h4::before{content:"";position:absolute;left:24px;top:27px;width:24px;height:24px;border-radius:50%;background:var(--white)}
.tweets{position:absolute;left:20px;top:72px;width:236px}
.tweets li{list-style:none;display:flex;gap:10px;height:80px;padding-top:10px;border-bottom:1px solid var(--sky-line)}
.tweets li:last-child{border-bottom:0}
.avatar{width:40px;height:40px;flex:none;background:linear-gradient(135deg,#e8d4b8,#b8926c);border:2px solid var(--white)}
.tweets p{font-size:11.5px;line-height:14px;color:var(--white)}
.tweets em{display:block;font-size:11px;color:#e6f6fd}

/* footer */
.foot-divider{position:absolute;left:560px;top:2878px;width:80px;height:2px;background:#dadada}
.site-footer{position:absolute;left:0;top:2896px;width:1200px;height:89px;background:var(--navy-deep);color:#e5edf2;font-size:13px;display:flex;align-items:center;justify-content:center}
</style>
</head>
<body>

<header class="site-header">
  <div class="brand">GlimStep</div>
  <div class="social-tabs" aria-label="Social links"><span></span><span></span><span></span><span></span></div>
</header>

<article class="post" style="top:206px">
  <h2>Lorem ipsum dolor sit amet, consectetur adipis cing elit Aliquam sagittis</h2>
  <div class="meta"><span>March 17, 2014.</span><span class="comments">&#9679; 5 Comments</span>
    <span class="share"><b>Like</b><i>3k</i><b>Post</b><i>316</i><b>+1</b><i>55</i></span></div>
  <div class="photo" role="img" aria-label="Ballroom couples dancing across a polished floor" style="width:680px;height:322px;background:linear-gradient(to bottom,#3a2a3e,#6b4a36 55%,#c7893f)"></div>
  <p>Lorem ipsum dolor sit amet, consectetur adipiscing elit. In fermentum dolor non augue pretium egestas. Donec sem eros, tincidunt at congue ut, posuere sit amet est. Vivamus scelerisque viverra odio sit amet laoreet. Ut nec neque non justo rutrum tempor lobortis eu ante.</p>
  <p>Aliquam sagittis, nibh quis commodo auctor, risus mauris laoreet lectus, id facilisis libero odio nec enim. Sed id ligula adipiscing purus lacinia aliquet. Sed eu est non nisl vehicula bibendum congue sit amet enim.</p>
  <a class="more">Continue Reading <span>&rarr;</span></a>
</article>
<div class="divider" style="top:877px"></div>

<article class="post" style="top:934px">
  <h2>Lorem ipsum amet, adipis cing aliquam agittis</h2>
  <div class="meta"><span>March 17, 2014.</span><span class="comments">&#9679; 5 Comments</span>
    <span class="share"><b>Like</b><i>3k</i><b>Post</b><i>316</i><b>+1</b><i>55</i></span></div>
  <div class="photo" role="img" aria-label="Latin dance couple posing in red and black costumes" style="width:512px;height:772px;margin-left:76px;background:linear-gradient(to bottom,#141010,#3b241c 50%,#a07048)"></div>
  <p>Lorem ipsum dolor sit amet, consectetur adipiscing elit. In fermentum dolor non augue pretium egestas. Donec sem eros, tincidunt at congue ut, posuere sit amet est. Vivamus scelerisque viverra odio sit amet laoreet. Ut nec neque non justo rutrum tempor lobortis eu ante.</p>
  <p>Aliquam sagittis, nibh quis commodo auctor, risus mauris laoreet lectus, id facilisis libero odio nec enim. Sed id ligula adipiscing purus lacinia aliquet. Sed eu est non nisl vehicula bibendum congue sit amet enim.</p>
  <a class="more">Continue Reading <span>&rarr;</span></a>
</article>
<div class="divider" style="top:2041px"></div>

<article class="post" style="top:2102px">
  <h2>Lorem ipsum amet, adipis cing aliquam agittis</h2>
  <div class="meta"><span>March 17, 2014.</span><span class="comments">&#9679; 5 Comments</span>
    <span class="share"><b>Like</b><i>3k</i><b>Post</b><i>316</i><b>+1</b><i>55</i></span></div>
  <div class="photo" role="img" aria-label="Dance couple in a dramatic dip on a dark stage" style="width:680px;height:436px;background:linear-gradient(to bottom,#1a1214,#3a1416)"></div>
  <p>Lorem ipsum dolor sit amet, consectetur adipiscing elit. In fermentum dolor non augue pretium egestas. Donec sem eros, tincidunt at congue ut, posuere sit amet est. Vivamus scelerisque viverra odio sit amet laoreet. Ut nec neque non justo rutrum tempor lobortis eu ante.</p>
  <p>Aliquam sagittis, nibh quis commodo auctor, risus mauris laoreet lectus, id facilisis libero odio nec enim. Sed id ligula adipiscing purus lacinia aliquet. Sed eu est non nisl vehicula bibendum congue sit amet enim.</p>
  <a class="more">Continue Reading <span>&rarr;</span></a>
</article>

<aside class="sidebar">
  <div class="ad-box"><span class="dot"></span><span class="name">Adveloq</span></div>
  <div class="tabs"><span class="on">Popular</span><span class="off">Events</span></div>
  <ul class="news">
    <li><span class="thumb"></span><div><em>March, 17, 2014</em><strong>Lorem ipsum dolor sit amet, consec tetur adip adips cing elit dolor sit amet,...</strong></div></li>
    <li><span class="thumb"></span><div><em>March, 17, 2014</em><strong>Lorem ipsum dolor sit amet, consec tetur adip adips cing elit dolor sit amet,...</strong></div></li>
    <li><span class="thumb"></span><div><em>March, 17, 2014</em><strong>Lorem ipsum dolor sit amet, consec tetu...</strong></div></li>
  </ul>
  <div class="read-all">Read All News <span>&rarr;</span></div>
  <div class="welcome">
    <h3>Welcome to<br>Glimmer Step Blog</h3>
    <p>Lorem ipsum dolor sit amet, consec tetur adipiscing elit. In fermentum dolor non augue pretium egestas. Donec tincidunt at congue ut, posuere sit amet est. Vivamus scelerisque viverra odio amet laoreet. Ut nec neque non justo rutrum tempor lobortis eu ante.</p>
    <p>Donec sem eros, tincidunt at congue ut, posuere sit amet est. Vivamus scelerisque viverra odio sit amet laoreet. Ut nec neque non justo rutrum tempor</p>
  </div>
  <div class="fb-btn"><span class="sq"></span>Find us on Circlebook</div>
  <div class="fan">
    <div class="fan-head"><span class="mark">GS</span><div><b>GlimStep</b><i>Like</i></div></div>
    <small>207 people like GlimStep</small>
    <div class="faces">
      <span>Tina Marsh</span><span>Paul Dane</span><span>Paul Dane</span><span>Jamie</span>
      <span>Jon Hale</span><span>Paul Dane</span><span>Paul Dane</span><span>Jamie</span>
    </div>
    <div class="plugin">Circlebook social plugin</div>
  </div>
</aside>

<section class="chirper">
  <h4>Chirper &nbsp;Follow</h4>
  <ul class="tweets">
    <li><span class="avatar"></span><div><p>GlimStep, lorem ipsum dolor sit amet, elit dolor sit amet...</p><em>2 hour ago, favourite, learn more</em></div></li>
    <li><span class="avatar"></span><div><p>GlimStep, lorem ipsum dolor sit amet, elit dolor sit amet...</p><em>2 hour ago, favourite, learn more</em></div></li>
    <li><span class="avatar"></span><div><p>GlimStep, lorem ipsum dolor sit amet, elit dolor sit amet...</p><em>2 hour ago, favourite, learn more</em></div></li>
    <li><span class="avatar"></span><div><p>GlimStep, lorem ipsum dolor sit amet, elit dolor sit amet...</p><em>2 hour ago, favourite, learn more</em></div></li>
  </ul>
</section>

<div class="foot-divider"></div>
<footer class="site-footer">All Right Reserved Copyright © 2014 &nbsp;/&nbsp; Terms and Conditions</footer>

</body>
</html>
```